Stationery Design Project for Nimbora, Chicago

Nimbora, a street parking application which helps car drivers find a street parking spot by offering an ideal path along which to look for parking. This path is calculated by our algorithm based on data (e.g. historical data, baseball games schedule, etc.). Along this path the driver will find a spot and will also save 70% of the search time. Customer we target is reg. between 21 and 45 yo.

We envision something young, fresh, bright and original. Slightly abstract maybe. It should represent the idea and elements of finding street parking in the city, e.g. car(s), parking spot, people, city, etc. (just ideas!).

Logo is attached.

Requirement:
- Business Cards (2 Sided Full Color CMYK)
- Letterhead (1 Sided Full Color CMYK)
- Envelope (1 Sided Full Color CMYK)
- Sticker (1 Sided Full Color CMYK), round with a 2inch diameter.

Reason: We're starting to get more and more designs and need more time to look into all of them. Very exciting!! Thanks to everybody!

Hi all, we're in the process of selecting our favs. Though choices!!! Really good submissions. Will keep you posted and sorry for the delay.

Target Market(s)

Car drivers and owners between 21 and 45

Industry/Entity Type

Parking

Requirements
Must have
• Sticker should be round and include company URL nimbora.com and the new logo which we will attach soon.
Should not have
• Should not be too serious or boring.

```html
<!DOCTYPE html>
<html lang="en">
<head>
<meta charset="utf-8">
<title>Nimbora Business Card</title>
<link rel="stylesheet" href="https://fonts.googleapis.com/css2?family=Open+Sans:wght@400;600;700&display=swap">
<style>
  :root {
    --page-bg: #e4e4e4;
    --card-white: #ffffff;
    --ink-dark: #1f1f22;
    --ink-grey: #4a4a4e;
    --name-navy: #283593;
    --accent-sky: #29a3dc;
    --rule-teal: #5cbab1;
    --band-navy: #2b3a92;
    --band-sky: #27a8e0;
    --back-blue: #1b78c2;
    --photo-deep: #3a7fb6;
    --photo-light: #6ea3cc;
    --mark-blue: #1f5fc0;
  }
  * { margin: 0; padding: 0; box-sizing: border-box; }
  html, body { width: 956px; height: 1200px; overflow: hidden; }
  body {
    background: var(--page-bg);
    font-family: "Open Sans", Arial, sans-serif;
    position: relative;
  }
  .card {
    position: absolute;
    border-radius: 28px;
    overflow: hidden;
    box-shadow: 0 4px 14px rgba(0,0,0,0.25);
  }
  .card-front {
    left: 76px; top: 96px; width: 797px; height: 457px;
    background: var(--card-white);
  }
  .brand-mark {
    position: absolute;
    left: 49px; top: 46px; width: 160px; height: 160px;
    border-radius: 50%;
    background: var(--mark-blue);
  }
  .brand-name {
    position: absolute;
    left: 238px; top: 60px;
    font-size: 96px; font-weight: 600; letter-spacing: 1px;
    color: var(--ink-dark);
    line-height: 1;
  }
  .holder {
    position: absolute; left: 84px; top: 305px;
  }
  .holder-name {
    font-size: 24px; font-weight: 700; color: var(--name-navy);
  }
  .holder-role {
    font-size: 20px; font-weight: 700; color: var(--accent-sky);
  }
  .holder-phones {
    margin-top: 6px;
    font-size: 19px; color: var(--ink-grey);
  }
  .holder-phones b { color: var(--ink-dark); }
  .address {
    position: absolute; right: 41px; top: 318px;
    text-align: right; font-size: 19px; line-height: 27px;
    color: var(--ink-grey);
  }
  .rule-teal {
    position: absolute; left: 0; top: 384px; width: 100%; height: 7px;
    background: var(--rule-teal);
  }
  .contact-band {
    position: absolute; left: 0; top: 396px; width: 100%; height: 61px;
    background: linear-gradient(90deg, var(--band-navy) 0%, var(--band-navy) 25%, var(--band-sky) 50%, var(--band-navy) 75%, var(--band-navy) 100%);
    color: #fff; font-size: 19px;
    display: flex; justify-content: center; padding-top: 6px;
  }
  .contact-band b { font-weight: 700; }
  .card-back {
    left: 73px; top: 650px; width: 798px; height: 455px;
    background: var(--back-blue);
  }
  .parking-photo {
    position: absolute; left: 24px; top: 22px; width: 751px; height: 410px;
    background: linear-gradient(180deg, var(--photo-light) 0%, var(--photo-deep) 45%, var(--photo-light) 100%);
  }
  .back-mark {
    position: absolute; left: 267px; top: 40px; width: 260px; height: 260px;
    border-radius: 50%;
    background: var(--mark-blue);
  }
  .back-name {
    position: absolute; left: 0; top: 320px; width: 798px;
    text-align: center; font-size: 88px; font-weight: 600;
    color: #fff; line-height: 1;
  }
</style>
</head>
<body>
  <section class="card card-front">
    <div class="brand-mark"></div>
    <div class="brand-name">nimbora</div>
    <div class="holder">
      <div><span class="holder-name">Your Name</span> <span class="holder-role">- Designation</span></div>
      <div class="holder-phones"><b>t</b> : 123-456-7890 &nbsp;|&nbsp; <b>c</b> : 123-456-7890</div>
    </div>
    <div class="address">City Name, Street Name<br>State Name, Country Code</div>
    <div class="rule-teal"></div>
    <div class="contact-band"><span><b>e</b> : name@website.com &nbsp;|&nbsp; <b>w</b> : www.website.com</span></div>
  </section>

  <section class="card card-back">
    <div class="parking-photo" role="img" aria-label="Blue-tinted photo of a large outdoor car park full of parked cars with trees behind"></div>
    <div class="back-mark"></div>
    <div class="back-name">nimbora</div>
  </section>
</body>
</html>
```